Profesional personal website needs design and business card

I need a business card with my professional name as a logo "Dorian Vitality" for my business. I am a Wellness Coach, consultant and trainer. So it should be professional, wellness oriented and modern.

Target Market(s)

Private clients, governments, corporations. Luxury and high market.

Industry/Entity Type

Health And Wellness

Contact Information for Business Card

Dorian Vitality should be the logo

Colors

Designer to choose colors to be used in the design.

Requirements
Must have
• Dorian Vitality
• Name: Tomás Lirandel
• Wellness Coach, Consultant & Trainer.
• Website: www.dorianvitality-example.com
• Phone:
• Spain (+34) 612 480 317
• (USA) +1 (555) 610 4829
Nice to have
• The most important is the design of "Dorian Vitality", as this is going to be my personal brand logo. It should be professional, wellness, high end and actual.
Should not have
• no golds, no baroque style..

```html
<!DOCTYPE html>
<html lang="en">
<head>
<meta charset="UTF-8">
<title>Dorian Vitality — Business Card</title>
<link rel="stylesheet" href="https://fonts.googleapis.com/css2?family=Arimo:wght@400;700&display=swap">
<style>
  :root {
    --backdrop: #2a2b2d;
    --card: #1b1d1c;
    --card-edge: #111312;
    --green: #2fb52a;
    --green-rule: #239a20;
    --ink: #e8ebe8;
  }
  * { margin: 0; padding: 0; box-sizing: border-box; }
  html, body {
    width: 1200px;
    height: 874px;
    overflow: hidden;
    background: var(--backdrop);
    font-family: "Arimo", Arial, sans-serif;
  }
  .stage {
    width: 1200px;
    height: 874px;
    display: flex;
    flex-direction: column;
    align-items: center;
    justify-content: center;
    gap: 26px;
  }
  .card {
    width: 580px;
    height: 331px;
    background: var(--card);
    border: 1px solid var(--card-edge);
    box-shadow: 0 14px 30px rgba(0, 0, 0, 0.45);
    position: relative;
  }
  .card-front {
    display: flex;
    align-items: center;
    justify-content: center;
  }
  .brand-name {
    color: var(--green);
    font-weight: 700;
    font-size: 58px;
    line-height: 0.95;
    letter-spacing: 1px;
    text-transform: uppercase;
    text-align: center;
  }
  .card-back {
    display: flex;
    align-items: flex-end;
    justify-content: center;
    padding-bottom: 64px;
  }
  .contact {
    text-align: center;
    color: var(--ink);
    text-transform: uppercase;
  }
  .person-name {
    color: var(--green);
    font-weight: 700;
    font-size: 24px;
    letter-spacing: 0.5px;
    margin-bottom: 4px;
  }
  .rule {
    height: 1px;
    background: var(--green-rule);
    width: 400px;
    margin: 0 auto;
  }
  .role {
    font-size: 13px;
    letter-spacing: 0.4px;
    margin: 6px 0 8px;
  }
  .phones {
    font-size: 14px;
    letter-spacing: 0.3px;
    margin-bottom: 7px;
  }
  .phones .divider { margin: 0 8px; }
  .website {
    font-size: 14px;
    letter-spacing: 0.3px;
    margin-top: 10px;
  }
</style>
</head>
<body>
  <main class="stage">
    <section class="card card-front">
      <h1 class="brand-name">Dorian<br>Vitality</h1>
    </section>
    <section class="card card-back">
      <div class="contact">
        <p class="person-name">Tomás Lirandel</p>
        <div class="rule"></div>
        <p class="role">Wellness Coach, Consultant &amp; Trainer</p>
        <p class="phones">(+34) 612 480 317 Spain<span class="divider">|</span>+1 (555) 610 4829 (USA)</p>
        <div class="rule"></div>
        <p class="website">www.dorianvitality-example.com</p>
      </div>
    </section>
  </main>
</body>
</html>
```